Tavel Website

Need a 4 page Drupal website - Home, About Us, Portfolio, Contact for a private equity/venture capital firm and new logo - company name is Tavel Corporation. The design should communicate - stock markets, hedge funds, deal-making, investments. The Portfolio section is to showcase the small companies we invest in. Hoping for something fresh, dynamic, even fun - no cliche financial images of New York. Not technical - but know how use Drupal content management to make text edits, blocks, articles, etc. We don't use any social media - so no chirply, Pagebook or WorkNode links. We need space for a post heron email sign-up form. Need website uploaded to my Corvane web hosting account. First time user of Sketch Plaza - have 3 other company websites that need refreshing.

```html
<!DOCTYPE html>
<html lang="en">
<head>
<meta charset="utf-8">
<title>Tavel Corporation</title>
<link rel="stylesheet" href="https://fonts.googleapis.com/css2?family=Bitter:wght@400;500&family=Open+Sans:wght@400;600&family=Roboto:wght@500;700&display=swap">
<style>
:root{
  --blue:#0b6aa6;
  --ink:#222;
  --line:#e2e2e2;
  --panel:#f3f4f6;
  --footer:#e4e4e4;
  --green:#3aa31c;
  --red:#d9261c;
  --bar:rgba(20,20,20,.82);
  --caption:rgba(40,40,40,.75);
}
*{box-sizing:border-box;margin:0;padding:0}
html,body{width:1038px;height:1200px;overflow:hidden;background:#fff}
body{position:relative;font-family:"Open Sans",Arial,sans-serif;color:var(--ink)}
h2,h3{font-weight:400}
.site-header{position:absolute;left:0;top:0;width:1038px;height:59px;background:#fff}
.brand{position:absolute;left:132px;top:13px;font-family:"Bitter",Georgia,serif;font-weight:500;font-size:21px;color:#1d4f8c;letter-spacing:.2px}
.main-nav{position:absolute;left:565px;top:15px;display:flex;gap:2px}
.main-nav a{display:block;width:83px;height:32px;line-height:32px;background:var(--blue);color:#fff;text-decoration:none;font-family:"Roboto",Arial,sans-serif;font-weight:500;font-size:12px;text-align:center}
.hero{position:absolute;left:0;top:59px;width:1038px;height:397px;background:linear-gradient(100deg,#6d7075 0%,#b9c0c8 30%,#8fa3b8 50%,#6b7d92 75%,#4d5663 100%)}
.hero-arrow{position:absolute;top:185px;width:30px;height:40px}
.hero-arrow.prev{left:84px}
.hero-arrow.next{left:928px}
.hero-caption-title{position:absolute;left:133px;top:236px;width:203px;height:28px;background:var(--caption);color:#fff;font-family:"Roboto",Arial,sans-serif;font-weight:500;font-size:13px;line-height:16px;padding:11px 0 0 12px}
.hero-caption-text{position:absolute;left:133px;top:264px;width:276px;height:48px;background:var(--caption);color:#fff;font-size:11px;line-height:16px;padding:6px 12px;white-space:nowrap}
.services{position:absolute;left:133px;top:467px;width:486px;height:321px}
.tile{position:absolute;width:240px;height:157px}
.tile .art{position:absolute;inset:0}
.tile .bar{position:absolute;left:0;bottom:0;width:100%;height:35px;background:var(--bar);color:#fff;font-family:"Bitter",Georgia,serif;font-size:14px;line-height:35px;padding-left:13px}
.tile .bar svg{position:absolute;right:10px;top:9px}
.tile .bar:after{content:"";position:absolute;right:36px;top:6px;width:1px;height:23px;background:#888}
.t1{left:0;top:0}.t2{left:245px;top:0}.t3{left:0;top:164px}.t4{left:245px;top:164px}
.t1 .art{background:linear-gradient(160deg,#1b3f9a,#0e2566 70%,#0a1a48)}
.t2 .art{background:linear-gradient(180deg,#d9d6d0,#c9a77a 55%,#e9e9ea)}
.t3 .art{background:linear-gradient(135deg,#f1f1f1,#6e7682 50%,#1e2a3c)}
.t4 .art{background:linear-gradient(180deg,#2f7fd0,#8ab8e2 60%,#e8edf0)}
.indices-title{position:absolute;left:630px;top:463px;font-family:"Bitter",Georgia,serif;font-size:15px;color:var(--blue)}
.indices{position:absolute;left:632px;top:489px;width:275px;height:299px;border:1px solid #cfcfcf;background:#fff}
.indices table{width:100%;border-collapse:collapse;font-family:"Bitter",Georgia,serif;font-size:10.5px}
.indices th{background:#f1f1f1;height:30px;font-weight:400;text-align:left;padding-left:12px;color:#222;border-bottom:1px solid #ddd}
.indices td{height:32px;border-bottom:1px solid var(--line);padding-left:12px;white-space:nowrap}
.indices tr:last-child td{border-bottom:none}
.indices td.last{color:#888;padding-left:8px}
.indices th.c2{padding-left:10px}
.indices td.up{color:var(--green)}
.indices td.down{color:var(--red)}
.indices td.buy{color:var(--green)}
.indices tbody tr td:first-child{padding-left:14px}
.portfolio-title{position:absolute;left:132px;top:809px;font-family:"Bitter",Georgia,serif;font-size:15px;color:var(--blue)}
.partners{position:absolute;left:133px;top:838px;width:773px;height:52px;display:flex;align-items:center;justify-content:space-between}
.partner{display:flex;align-items:center;gap:5px;font-weight:600;font-size:15px;color:#2b2b4a}
.partner i{display:block;width:10px;height:10px;background:#2b2b4a}
.welcome-title{position:absolute;left:133px;top:906px;font-family:"Bitter",Georgia,serif;font-size:15px;color:var(--blue)}
.welcome{position:absolute;left:133px;top:931px;width:773px;height:120px;background:var(--panel);padding:10px 15px}
.welcome p{font-size:10.5px;line-height:17.6px;color:#333;white-space:nowrap}
.read-more{position:absolute;left:17px;top:88px;height:19px;width:67px;background:var(--blue);color:#fff;font-size:10px;font-weight:600;text-align:center;line-height:19px;text-decoration:none}
.site-footer{position:absolute;left:0;top:1062px;width:1038px;height:138px;background:var(--footer)}
.newsletter-title{position:absolute;left:132px;top:16px;font-family:"Bitter",Georgia,serif;font-size:13px;letter-spacing:.3px;color:#111}
.newsletter-text{position:absolute;left:132px;top:37px;font-size:11px;line-height:16px;color:#222}
.signup{position:absolute;left:133px;top:80px;width:276px;height:34px;background:#fff;border:1px solid #bdbdbd}
.signup svg.mail{position:absolute;left:11px;top:12px}
.signup span{position:absolute;left:28px;top:10px;font-size:9.5px;color:#333;letter-spacing:.2px}
.signup .go{position:absolute;right:-1px;top:-1px;width:32px;height:34px;background:var(--blue)}
.signup .go svg{position:absolute;left:10px;top:10px}
.footer-nav{position:absolute;right:132px;top:73px;font-size:11px;color:#333}
.footer-nav a{color:#333;text-decoration:none}
.footer-nav .sep{margin:0 9px}
.copyright{position:absolute;right:132px;top:97px;font-size:11px;color:#333}
</style>
</head>
<body>
<header class="site-header">
  <div class="brand">Tavel Corporation</div>
  <nav class="main-nav">
    <a href="#">HOME</a><a href="#">ABOUT US</a><a href="#">PORTFOLIO</a><a href="#">CONTACT</a>
  </nav>
</header>

<section class="hero" role="img" aria-label="Hand touching a glowing financial chart with bar graphs and line graphs over a world map">
  <svg class="hero-arrow prev" viewBox="0 0 30 40"><polyline points="22,4 8,20 22,36" fill="none" stroke="#fff" stroke-width="5"/></svg>
  <svg class="hero-arrow next" viewBox="0 0 30 40"><polyline points="8,4 22,20 8,36" fill="none" stroke="#fff" stroke-width="5"/></svg>
  <div class="hero-caption-title">EQUITY &amp; VENTURE CAPITAL</div>
  <div class="hero-caption-text">Lorem Ipsum is simply dummy text of the printing<br>and typesetting industry</div>
</section>

<section class="services">
  <div class="tile t1"><div class="art" role="img" aria-label="Blue stock ticker screen with percentage figures"></div><div class="bar">Stock Markets<svg width="12" height="16" viewBox="0 0 12 16"><polyline points="3,2 9,8 3,14" fill="none" stroke="#fff" stroke-width="2.5"/></svg></div></div>
  <div class="tile t2"><div class="art" role="img" aria-label="Stacks of coins on a financial document"></div><div class="bar">Hedge Funds<svg width="12" height="16" viewBox="0 0 12 16"><polyline points="3,2 9,8 3,14" fill="none" stroke="#fff" stroke-width="2.5"/></svg></div></div>
  <div class="tile t3"><div class="art" role="img" aria-label="Business people shaking hands over a desk"></div><div class="bar">Deal-making<svg width="12" height="16" viewBox="0 0 12 16"><polyline points="3,2 9,8 3,14" fill="none" stroke="#fff" stroke-width="2.5"/></svg></div></div>
  <div class="tile t4"><div class="art" role="img" aria-label="Hand dropping a coin into a piggy bank under a blue sky"></div><div class="bar">Investments<svg width="12" height="16" viewBox="0 0 12 16"><polyline points="3,2 9,8 3,14" fill="none" stroke="#fff" stroke-width="2.5"/></svg></div></div>
</section>

<h2 class="indices-title">Market Indices</h2>
<div class="indices">
  <table>
    <thead><tr><th>Name</th><th class="c2">Last</th><th>Change</th><th>Today</th></tr></thead>
    <tbody>
      <tr><td>Meridian 500</td><td class="last">2,000.13</td><td class="up">+0.11</td><td class="buy">80% Buy</td></tr>
      <tr><td>Crest 30</td><td class="last">2,000.13</td><td class="up">+8.73</td><td class="buy">80% Buy</td></tr>
      <tr><td>Techline</td><td class="last">2,000.13</td><td class="up">+0.46</td><td class="buy">80% Buy</td></tr>
      <tr><td>Harbor Comp</td><td class="last">2,000.13</td><td class="up">+10.78</td><td class="buy">80% Buy</td></tr>
      <tr><td>Kestrel Index</td><td class="last">2,000.13</td><td class="up">-0.25</td><td class="buy">80% Buy</td></tr>
      <tr><td>Alder 1000</td><td class="last">2,000.13</td><td class="up">-0.02</td><td class="buy">80% Buy</td></tr>
      <tr><td>Alder 2000</td><td class="last">2,000.13</td><td class="down">-0.04</td><td class="buy">80% Buy</td></tr>
      <tr><td>Alder 3000</td><td class="last">2,000.13</td><td class="down">-0.04</td><td class="buy">80% Buy</td></tr>
    </tbody>
  </table>
</div>

<h2 class="portfolio-title">Portfolio</h2>
<div class="partners">
  <span class="partner">Lumen Solar</span>
  <span class="partner">Vextra</span>
  <span class="partner"><i></i>Pondway</span>
  <span class="partner">Swiftline</span>
  <span class="partner">Nanoria</span>
  <span class="partner">Melor</span>
  <span class="partner"><i></i>Isleo</span>
  <span class="partner">Vitacore</span>
</div>

<h2 class="welcome-title">Welcome to our site</h2>
<section class="welcome">
  <p>Lorem Ipsum is simply dummy text of the printing and typesetting industry. Lorem Ipsum has been the industry's standard dummy text ever since the<br>1500s, when an unknown printer took a galley of type and scrambled it to make a type specimen book. It has survived not only five centuries, but also<br>the leap into electronic typesetting, remaining essentially unchanged&nbsp; It was popularised in the 1960s with the release of Linotone sheets containing<br>Lorem Ipsum passages, and more recently with desktop publishing software like Pagewell.</p>
  <a class="read-more" href="#">READ MORE</a>
</section>

<footer class="site-footer">
  <h3 class="newsletter-title">NEWSLETTER</h3>
  <p class="newsletter-text">Lorem Ipsum is simply dummy text of the printing and typesetting industry.<br>Lorem Ipsum has been the industry's standard dumm</p>
  <div class="signup">
    <svg class="mail" width="13" height="10" viewBox="0 0 13 10"><rect x="0.5" y="0.5" width="12" height="9" fill="none" stroke="#666"/><polyline points="0.5,0.5 6.5,5.5 12.5,0.5" fill="none" stroke="#666"/></svg>
    <span>E MAIL ADDRESS</span>
    <div class="go"><svg width="12" height="16" viewBox="0 0 12 16"><polyline points="3,2 9,8 3,14" fill="none" stroke="#fff" stroke-width="2.5"/></svg></div>
  </div>
  <nav class="footer-nav"><a href="#">Home</a><span class="sep">|</span><a href="#">About Us</a><span class="sep">|</span><a href="#">Portfolio</a><span class="sep">|</span><a href="#">Contact</a></nav>
  <p class="copyright">Copyrights @ 2014 All Rights</p>
</footer>
</body>
</html>
```